Beacon Advisory Website

I currently have a website www.beaconadvisoryinc.com. We are a IT Consulting Company. Our website will pretty much tell out our services. I am looking to enhance my website and make it look more professional. Looking for very classy and Contemporary look and design for my website.

It Company

```html
<!DOCTYPE html>
<html lang="en">
<head>
<meta charset="utf-8">
<title>Beacon Advisory — IT Consulting</title>
<link href="https://fonts.googleapis.com/css2?family=Oswald:wght@400&family=Roboto:wght@300;400;500&display=swap" rel="stylesheet">
<style>
:root{
  --blue:#0d5fa9;
  --blue-dark:#0a4f8e;
  --blue-footer:#0b5aa5;
  --ink:#333;
  --muted:#666;
  --rule:#9a9a9a;
  --band:#e7e7e7;
  --white:#fff;
  --icon-dark:#555;
}
*{margin:0;padding:0;box-sizing:border-box}
html,body{width:712px;height:1200px;overflow:hidden;background:var(--white)}
body{position:relative;font-family:"Roboto",Arial,sans-serif;color:var(--ink)}

/* Header */
.site-header{position:absolute;left:0;top:0;width:712px;height:64px;background:var(--white)}
.brand{position:absolute;left:60px;top:20px;display:flex;align-items:center;gap:7px}
.brand-mark{width:22px;height:22px;border-radius:50%;background:var(--blue)}
.brand-name{font-size:14px;font-weight:500;color:var(--blue);letter-spacing:.3px}
.main-nav{position:absolute;left:320px;top:0;height:64px;display:flex}
.main-nav a{display:flex;align-items:center;height:64px;padding:0 9px;font-size:7.4px;color:var(--ink);text-decoration:none;letter-spacing:.2px}
.main-nav a.is-active{background:var(--blue);color:var(--white);padding:0 9px}

/* Hero */
.hero{position:absolute;left:0;top:64px;width:712px;height:353px;
  background:radial-gradient(ellipse at 35% 55%,#6a5a52 0%,#3a3533 35%,#1f2224 70%,#16181a 100%)}
.hero-title{position:absolute;left:0;width:712px;top:192px;text-align:center;font-family:"Oswald",sans-serif;font-size:29px;color:var(--white);letter-spacing:-.3px}
.hero-sub{position:absolute;left:0;width:712px;top:236px;text-align:center;font-weight:300;font-size:17.5px;color:var(--white)}
.hero-dots{position:absolute;top:320px;left:310px;display:flex;gap:12px}
.hero-dots span{width:20px;height:3px;background:#5a5a5a}
.hero-dots span.is-current{width:28px;background:#cfcfcf}

/* Section titles */
.section-title{position:absolute;left:0;width:712px;text-align:center;font-weight:300;font-size:21px;color:var(--blue)}
.section-rule{position:absolute;height:1.5px;background:var(--rule)}

/* Buttons */
.btn{position:absolute;height:23px;display:flex;background:var(--blue);color:var(--white);font-size:7px;font-weight:500;text-decoration:none}
.btn-label{flex:1;display:flex;align-items:center;justify-content:center}
.btn-icon{width:22px;background:var(--blue-dark);display:flex;align-items:center;justify-content:center}

/* Welcome */
.welcome-text{position:absolute;left:72px;width:568px;top:474px;text-align:center;font-size:6.4px;line-height:12px;color:var(--muted)}

/* What we do */
.services{position:absolute;left:0;top:561px;width:712px;height:296px;background:var(--band)}
.service{position:absolute;top:76px;width:200px;text-align:center}
.service-icon{display:block;margin:0 auto}
.service-name{margin-top:14px;font-size:11px;letter-spacing:.3px;color:var(--ink)}
.service-text{margin-top:8px;font-size:6.4px;line-height:12px;color:var(--muted);padding:0 16px}

/* Testimonials */
.portrait{position:absolute;border-radius:50%;border:1.5px solid #bbb;background:radial-gradient(circle at 50% 40%,#d9cfc8 0%,#9a8e87 60%,#6d6560 100%)}
.portrait.is-side{background:radial-gradient(circle at 50% 40%,#9c9794 0%,#6f6b69 60%,#4f4c4a 100%)}
.carousel-arrow{position:absolute;top:955px}
.quote{position:absolute;left:150px;width:412px;top:1035px;text-align:center;font-size:10px;line-height:15px;color:var(--ink)}
.quote-mark{position:absolute;font-family:Georgia,serif;font-size:58px;color:#c8c8c8;line-height:1}
.quote-author{position:absolute;top:1076px;left:0;width:712px;display:flex;justify-content:center;align-items:center;gap:8px;font-size:8.5px;color:var(--blue);font-weight:500}
.quote-author i{width:48px;height:2px;background:#444}

/* Footer */
.site-footer{position:absolute;left:0;top:1115px;width:712px;height:85px;background:var(--blue-footer)}
.social{position:absolute;top:27px;left:298px;display:flex;gap:19px}
.social span{width:15px;height:15px;border-radius:3px;background:var(--white)}
.copyright{position:absolute;top:57px;left:0;width:712px;text-align:center;font-size:6.6px;color:var(--white)}
</style>
</head>
<body>

<header class="site-header">
  <div class="brand"><span class="brand-mark"></span><span class="brand-name">BEACON ADVISORY</span></div>
  <nav class="main-nav">
    <a class="is-active">COMPANY</a>
    <a>SERVICES</a>
    <a>SOLUTIONS</a>
    <a>RESOURCES</a>
    <a>CAREER</a>
    <a>CONTACT US</a>
  </nav>
</header>

<section class="hero" role="img" aria-label="Two business people shaking hands, dark toned photo">
  <h1 class="hero-title">BEACON ADVISORYINC</h1>
  <p class="hero-sub">MEETING THESE DEMANDS FOR OVER 25 YEARS</p>
  <div class="hero-dots"><span></span><span class="is-current"></span><span></span></div>
</section>

<h2 class="section-title" style="top:431px">WELCOME !</h2>
<div class="section-rule" style="left:269px;width:174px;top:461px"></div>
<p class="welcome-text">Today's IT market is a dynamic, fast-paced industry, with ever-increasing demands. Meeting these demands for over 25 years, Beacon Advisory maintains a global presence, aggressively recruiting expertly qualified IT and Management Professionals from around the world and cultivating key partnerships with corporations to understand their business models end-to-end, with a goal of delivering exceptional client service and ensuring a consistent delivery of the talent needed to drive results.</p>
<a class="btn" style="left:317px;top:519px;width:78px"><span class="btn-label">MORE INFO</span><span class="btn-icon"><svg width="9" height="9" viewBox="0 0 10 10"><circle cx="3.5" cy="6" r="2.4" fill="none" stroke="#fff" stroke-width="1.4"/><circle cx="7.5" cy="3" r="1.6" fill="none" stroke="#fff" stroke-width="1.2"/></svg></span></a>

<section class="services">
  <h2 class="section-title" style="top:18px">WHAT WE DO</h2>
  <div class="section-rule" style="left:269px;width:174px;top:47px"></div>

  <div class="service" style="left:44px">
    <svg class="service-icon" width="104" height="104" viewBox="0 0 104 104">
      <circle cx="52" cy="52" r="51" fill="#c9c9c9"/><circle cx="52" cy="52" r="46" fill="#b3b3b3"/>
      <circle cx="52" cy="52" r="38" fill="var(--icon-dark)"/>
      <path d="M32 46 L42 40 L52 44 L62 40 L72 46 L72 56 L60 66 L44 66 L32 56Z" fill="#fff"/>
    </svg>
    <h3 class="service-name">CONSULTING</h3>
    <p class="service-text">Beacon Advisory has certified professional consultants to work with you to help increase</p>
  </div>

  <div class="service" style="left:256px">
    <svg class="service-icon" width="104" height="104" viewBox="0 0 104 104">
      <circle cx="52" cy="52" r="51" fill="#c9c9c9"/><circle cx="52" cy="52" r="46" fill="#b3b3b3"/>
      <circle cx="52" cy="52" r="38" fill="var(--blue)"/>
      <circle cx="46" cy="47" r="8" fill="none" stroke="#fff" stroke-width="5" stroke-dasharray="3 2.2"/>
      <circle cx="46" cy="47" r="3" fill="#fff"/>
      <circle cx="60" cy="55" r="5.5" fill="none" stroke="#fff" stroke-width="4" stroke-dasharray="2.4 1.8"/>
      <circle cx="48" cy="63" r="4.5" fill="none" stroke="#fff" stroke-width="3.5" stroke-dasharray="2 1.6"/>
    </svg>
    <h3 class="service-name">STAFF AUGMENTATION</h3>
    <p class="service-text">For years Beacon Advisory has been offering our customers the ability to augment their existing staff</p>
  </div>

  <div class="service" style="left:469px">
    <svg class="service-icon" width="104" height="104" viewBox="0 0 104 104">
      <circle cx="52" cy="52" r="51" fill="#c9c9c9"/><circle cx="52" cy="52" r="46" fill="#b3b3b3"/>
      <circle cx="52" cy="52" r="38" fill="var(--icon-dark)"/>
      <polygon points="52,34 57,46 70,46 60,54 64,67 52,59 40,67 44,54 34,46 47,46" fill="#fff"/>
    </svg>
    <h3 class="service-name">OFFSHORE</h3>
    <p class="service-text">Our Offshore development model has a unique distinction of providing efficient software</p>
  </div>

  <a class="btn" style="left:105px;top:247px;width:78px"><span class="btn-label">READ MORE</span><span class="btn-icon"><svg width="9" height="9" viewBox="0 0 10 10"><circle cx="3.5" cy="6" r="2.4" fill="none" stroke="#fff" stroke-width="1.4"/><circle cx="7.5" cy="3" r="1.6" fill="none" stroke="#fff" stroke-width="1.2"/></svg></span></a>
  <a class="btn" style="left:317px;top:247px;width:78px"><span class="btn-label">READ MORE</span><span class="btn-icon"><svg width="9" height="9" viewBox="0 0 10 10"><circle cx="3.5" cy="6" r="2.4" fill="none" stroke="#fff" stroke-width="1.4"/><circle cx="7.5" cy="3" r="1.6" fill="none" stroke="#fff" stroke-width="1.2"/></svg></span></a>
  <a class="btn" style="left:530px;top:247px;width:78px"><span class="btn-label">READ MORE</span><span class="btn-icon"><svg width="9" height="9" viewBox="0 0 10 10"><circle cx="3.5" cy="6" r="2.4" fill="none" stroke="#fff" stroke-width="1.4"/><circle cx="7.5" cy="3" r="1.6" fill="none" stroke="#fff" stroke-width="1.2"/></svg></span></a>
</section>

<h2 class="section-title" style="top:875px">WHAT OUR CLIENTS SAY</h2>
<div class="section-rule" style="left:228px;width:256px;top:904px"></div>

<svg class="carousel-arrow" style="left:60px" width="25" height="25" viewBox="0 0 25 25"><circle cx="12.5" cy="12.5" r="11.5" fill="none" stroke="#ddd" stroke-width="1.2"/><path d="M15 12.5H9M12 9.5L9 12.5L12 15.5" fill="none" stroke="#ddd" stroke-width="1.4"/></svg>
<svg class="carousel-arrow" style="left:627px" width="25" height="25" viewBox="0 0 25 25"><circle cx="12.5" cy="12.5" r="11.5" fill="none" stroke="#ddd" stroke-width="1.2"/><path d="M10 12.5H16M13 9.5L16 12.5L13 15.5" fill="none" stroke="#ddd" stroke-width="1.4"/></svg>

<div class="portrait is-side" style="left:232px;top:926px;width:88px;height:88px" role="img" aria-label="Client portrait"></div>
<div class="portrait is-side" style="left:391px;top:926px;width:88px;height:88px" role="img" aria-label="Client portrait"></div>
<div class="portrait" style="left:304px;top:914px;width:104px;height:104px" role="img" aria-label="Featured client portrait"></div>

<span class="quote-mark" style="left:144px;top:1017px">“</span>
<span class="quote-mark" style="left:488px;top:1046px">”</span>
<p class="quote">NORTHGATE ARE VERY GOOD AT DESIGNING A SYSTEM AROUND YOUR BUSINESS RATHER THAN YOUR BUSINESS AROUND THEIR SYSTEM.</p>
<div class="quote-author"><i></i>LENA MORROW<i></i></div>

<footer class="site-footer">
  <div class="social"><span></span><span></span><span></span><span></span></div>
  <p class="copyright">© 2016 beaconadvisoryinc.com.&nbsp; All Rights Reserved</p>
</footer>

</body>
</html>
```